Bramble Hounds Dog Behaviour, Training and Natural Healthcare Website

Hey there,
I need a webpage designed for my new business. It needs to be something authentic, new, fresh and representative of my business ethos. I operate out of Newcastle, NSW. I believe my job is to keep dogs alive and in their home by promoting communication and connection between dogs and their owners. This can't be achieved through training and behaviour alone. Nutritional guidance and environmental adaptation are often needed to complete the package and increase the success rate for these programs. I provide practical services such as walking coaching, nutrition profiling, behavioural modification, puppy minding, board and train programs for puppies and young dogs, training, basic and complex skills training, physical therapies and natural healthcare options. In effect taking care of the whole dog.
My motto is = Happy dogs, happy owners.
My catch cry is = promoting communication and connection between dogs and their owners.

I have in mind pages that can also link to other pages when an icon is clicked. I need a homepage, sections to explain what each of my services do (4 - which could be independent pages so I can attach photos) and a gallery. I want to have multi page function, an online capability for future retail, ability to amend and update content myself, an online booking and payment facility. My interests lie in I have seen many successes via and environmental modifications.
I've attached the logo which features prominently on my business card and Facebook page. The corporate colours are Blue with a splash of red and white. The dog being held in the healing hands must feature.

Thanks!

Target Market(s)

Australian Pet Dog Owners

Industry/Entity Type

Communication

Coding

Colors
0355a3
ec1f27
ffffff

Requirements
Must have
• The business colours (blue with a splash of red and white), the dog in the healing hands
Should not have
• Pawprints or cartoon animals

```html
<!DOCTYPE html>
<html lang="en">
<head>
<meta charset="utf-8">
<title>Bramble Hounds – Dog Behaviour, Training and Natural Healthcare</title>
<link rel="stylesheet" href="https://fonts.googleapis.com/css2?family=Raleway:wght@400;500;600&family=Open+Sans:wght@400;600&display=swap">
<style>
:root{
  --blue:#0355a3;
  --blue-light:#1a86d0;
  --blue-dark:#04408a;
  --red:#ec1f27;
  --red-dark:#c9141b;
  --white:#ffffff;
  --grey-bg:#e6e6e6;
  --grey-panel:#f2f2f2;
  --text:#4a4a4a;
  --text-soft:#777777;
  --amber:#f2b418;
  --grey-icon:#8a8a8a;
  --footer:#f1f1f1;
}
*{box-sizing:border-box;margin:0;padding:0}
html,body{width:1168px;height:1200px;overflow:hidden}
body{position:relative;font-family:"Open Sans",Arial,sans-serif;color:var(--text);background:var(--white)}
a{text-decoration:none;color:inherit}

.top-band{position:absolute;left:0;top:0;width:1168px;height:87px;background:linear-gradient(#0a86cf,#0a62b4)}
.nav-band{position:absolute;left:0;top:87px;width:1168px;height:41px;background:linear-gradient(#f6363c,var(--red-dark))}
.call{position:absolute;right:132px;top:36px;text-align:right;font-family:"Raleway",sans-serif}
.call small{display:block;font-size:14px;color:#0a4b8e;line-height:16px}
.call strong{display:flex;align-items:center;gap:4px;font-weight:500;font-size:17px;color:var(--white)}
.main-nav{position:absolute;left:347px;top:87px;height:41px;display:flex;font-family:"Raleway",sans-serif;font-size:14.5px;color:var(--white)}
.main-nav a{display:flex;align-items:center;padding:0 19px;border-right:1px solid rgba(0,0,0,.12);border-left:1px solid rgba(255,255,255,.14)}
.main-nav a:first-child{border-left:0}
.main-nav a:last-child{border-right:0}

.brand{position:absolute;left:131px;top:0;width:216px;height:167px;background:linear-gradient(#1a78c8,var(--blue-dark));border-radius:0 0 6px 6px;box-shadow:0 4px 8px rgba(0,0,0,.3);text-align:center;color:var(--white);z-index:3}
.brand-mark{display:block;width:76px;height:76px;margin:14px auto 0;border-radius:50%;background:#f3e7c0}
.brand-name{display:block;margin-top:14px;font-family:"Raleway",sans-serif;font-weight:600;font-size:19px;letter-spacing:.5px}
.brand-motto{display:block;margin-top:4px;font-family:"Raleway",sans-serif;font-size:11.5px;letter-spacing:.2px}

.feature-zone{position:absolute;left:0;top:128px;width:1168px;height:628px;background:linear-gradient(#f7f7f7,var(--grey-bg))}
.swoosh{position:absolute;left:0;top:300px}
.hero{position:absolute;left:132px;top:128px;width:903px;height:375px;background:linear-gradient(180deg,#b9cde0 0%,#5d7a5c 35%,#486a76 58%,#6f9a3c 78%,#5c8a2e 100%)}
.hero-caption{position:absolute;left:57px;top:110px;width:327px;height:149px;background:rgba(3,85,163,.88);padding:22px 22px 0 28px;color:var(--white)}
.hero-caption h1{font-family:"Raleway",sans-serif;font-weight:400;font-size:27px;line-height:32px;white-space:nowrap}
.hero-caption h2{font-family:"Raleway",sans-serif;font-weight:400;font-size:15px;margin-top:2px;white-space:nowrap}
.hero-caption p{font-size:8.5px;line-height:15px;margin-top:9px;color:#b9d3ee;width:250px}
.dots{position:absolute;left:424px;top:355px;display:flex;gap:5px}
.dots i{width:10px;height:10px;border-radius:50%;background:var(--white)}

.services{position:absolute;left:132px;top:519px;display:flex;gap:14px}
.service{width:215px;height:214px;background:linear-gradient(135deg,#fff 60%,#f1f1f1);border:1px solid #dcdcdc;text-align:center;padding-top:20px}
.service-icon{display:block;width:75px;height:75px;border-radius:50%;margin:0 auto}
.service h3{font-family:"Raleway",sans-serif;font-weight:400;font-size:18px;line-height:19px;margin:18px 0 6px;height:19px;display:flex;align-items:flex-end;justify-content:center}
.service h3.two-line{height:38px;margin-top:11px}
.service p{font-size:10px;line-height:17px;color:var(--text-soft);padding:0 16px}
.service .more{display:block;margin-top:6px;font-size:11.5px;font-weight:600;color:#555}
.c-red{color:var(--red)} .c-amber{color:var(--amber)} .c-blue{color:var(--blue)} .c-grey{color:#666}
.bg-red{background:var(--red)} .bg-amber{background:var(--amber)} .bg-blue{background:var(--blue)} .bg-grey{background:var(--grey-icon)}

.about{position:absolute;left:133px;top:812px;width:280px}
.about h2{font-family:"Raleway",sans-serif;font-weight:400;font-size:19.5px;color:#333;white-space:nowrap}
.about h4{font-weight:400;font-size:12px;margin:12px 0 7px;color:#444}
.about p{font-size:10px;line-height:17px;margin-bottom:6px}
.btn{position:absolute;display:flex;align-items:center;justify-content:center;height:30px;border-radius:3px;font-size:11.5px;font-weight:600;color:var(--white);text-transform:uppercase}
.btn-blue{background:linear-gradient(#1b74c6,var(--blue))}
.btn-red{background:linear-gradient(#e52a30,var(--red-dark))}

.panel-method{position:absolute;left:432px;top:781px;width:303px;height:289px;background:linear-gradient(#ececec,#f8f8f8);border:1px solid #dedede}
.panel-blog{position:absolute;left:735px;top:781px;width:298px;height:289px;background:linear-gradient(#fafafa,#f1f1f1);border:1px solid #e3e3e3;border-left:0}
.panel-method h2,.panel-blog h2{font-family:"Raleway",sans-serif;font-weight:400;font-size:19.5px;position:absolute}
.panel-method h2{left:25px;top:33px;color:var(--red)}
.panel-blog h2{left:32px;top:30px;color:var(--blue)}
.method-photo{position:absolute;left:25px;top:61px;width:258px;height:98px;background:linear-gradient(90deg,#7b9bd8,#9eb7e6 60%,#6f8fcf)}
.panel-method p{position:absolute;left:25px;top:170px;width:260px;font-size:10px;line-height:17px}
.blog-list{position:absolute;left:32px;top:64px;width:250px;list-style:none}
.blog-list li{margin-bottom:9px}
.blog-list strong{display:block;font-weight:400;font-size:11.5px;color:#333;margin-bottom:3px}
.blog-list span{font-size:10px;line-height:17px;display:block}

.site-footer{position:absolute;left:0;top:1100px;width:1168px;height:100px;background:var(--footer);border-top:1px solid #dadada}
.footer-nav{position:absolute;left:136px;top:24px;font-family:"Raleway",sans-serif;font-size:12px;color:#555}
.footer-nav .sep{margin:0 5px}
.copyright{position:absolute;left:136px;top:49px;font-size:10.5px;color:#666}
.social{position:absolute;right:136px;top:23px;display:flex;gap:10px}
.social span{width:19px;height:19px;border-radius:50%;background:#777}
</style>
</head>
<body>

<header>
  <div class="top-band"></div>
  <div class="nav-band"></div>
  <a class="brand" href="#">
    <span class="brand-mark" role="img" aria-label="Bramble Hounds emblem"></span>
    <span class="brand-name">BRAMBLE HOUNDS</span>
    <span class="brand-motto">HAPPY DOGS, HAPPY OWNERS</span>
  </a>
  <div class="call">
    <small>Call Us Now</small>
    <strong>
      <svg width="15" height="15" viewBox="0 0 24 24" aria-hidden="true"><path fill="#fff" d="M6.6 10.8a15.1 15.1 0 0 0 6.6 6.6l2.2-2.2c.3-.3.7-.4 1-.2 1.1.4 2.3.6 3.6.6.6 0 1 .4 1 1V20c0 .6-.4 1-1 1A17 17 0 0 1 3 4c0-.6.4-1 1-1h3.5c.6 0 1 .4 1 1 0 1.3.2 2.5.6 3.6.1.3 0 .7-.2 1z"/></svg>
      555.014.2290
    </strong>
  </div>
  <nav class="main-nav">
    <a href="#">Home</a><a href="#">About Us</a><a href="#">Services</a><a href="#">Dog Training</a><a href="#">Testimonials</a><a href="#">Dog Care</a><a href="#">Contact</a>
  </nav>
</header>

<main>
  <section class="feature-zone">
    <svg class="swoosh" width="1168" height="130" viewBox="0 0 1168 130" aria-hidden="true">
      <path d="M0 95 Q300 10 600 50 T1168 40" fill="none" stroke="#d2d2d2" stroke-width="14"/>
      <path d="M0 120 Q320 40 620 80 T1168 80" fill="none" stroke="#dcdcdc" stroke-width="8"/>
    </svg>
  </section>

  <section class="hero" role="img" aria-label="Woman playing fetch with a brown dog on a lakeside meadow below snowy mountains">
    <div class="hero-caption">
      <h1>Dog Training &amp; Care</h1>
      <h2>Vivamus porttitor purus nisi eleifend</h2>
      <p>Ut nisi erat fermentum vel congue id euismod in elit Fusce ultricies orci ac feugiat suscipit leo massa sodales</p>
    </div>
    <div class="dots"><i></i><i></i><i></i><i></i></div>
  </section>

  <section class="services">
    <article class="service">
      <span class="service-icon bg-red" role="img" aria-label="First aid kit icon"></span>
      <h3 class="c-red">Dog Training</h3>
      <p>Aetur ridiculus mus In iaculis facilisis massa Etiam urna Sed porta</p>
      <a class="more" href="#">READ MORE</a>
    </article>
    <article class="service">
      <span class="service-icon bg-amber" role="img" aria-label="Food bowl icon"></span>
      <h3 class="c-amber">Nutrition Profiling</h3>
      <p>Aetur ridiculus mus In iaculis facilisis massa Etiam urna Sed porta</p>
      <a class="more" href="#">READ MORE</a>
    </article>
    <article class="service">
      <span class="service-icon bg-blue" role="img" aria-label="Bone icon"></span>
      <h3 class="c-blue two-line">Behavioural<br>Modification</h3>
      <p>Aetur ridiculus mus In iaculis facilisis massa Etiam urna Sed porta</p>
      <a class="more" href="#">READ MORE</a>
    </article>
    <article class="service">
      <span class="service-icon bg-grey" role="img" aria-label="Heart shaped bone icon"></span>
      <h3 class="c-grey">Health Care</h3>
      <p>Aetur ridiculus mus In iaculis facilisis massa Etiam urna Sed porta</p>
      <a class="more" href="#">READ MORE</a>
    </article>
  </section>

  <section class="about">
    <h2>ABOUT BRAMBLE HOUNDS</h2>
    <h4>Mauris vel lacus vitae felis vestibulum volutpat</h4>
    <p>nascetur ridiculus mus In iaculis facilisis massa Etiam eu urna Sed porta Suspendisse quam leo molestie sed luctus quis feugiat in pede Fusce tellus Sed metus augue convallis et vehicula ut pulvinar eu ante Integer orci tellus</p>
    <p>Class aptent taciti sociosqu ad litora torquent per conubia nostra per inceptos hymenaeos Proin nulla arcu Class aptent taciti sociosqu ad litora torquent per</p>
  </section>
  <a class="btn btn-blue" href="#" style="left:135px;top:1013px;width:102px">Read More</a>

  <section class="panel-method">
    <h2>How We Training</h2>
    <div class="method-photo" role="img" aria-label="Woman giving a hand signal to a golden retriever under a blue sky"></div>
    <p>Aliquet felis at cursus magna nisl nec elit Praesent elementum elit at tellus nec ultricies sit amet porttitor mattis enim In massa libero interdum nec</p>
    <a class="btn btn-red" href="#" style="left:22px;top:231px;width:102px">Read More</a>
  </section>

  <section class="panel-blog">
    <h2>Latest Blog Post</h2>
    <ul class="blog-list">
      <li><strong>Aascetur ridiculus mus iaculis</strong><span>molestie sed luctus quis feugiat in pede Fusce tellus etus augue aliquet felis at cursus</span></li>
      <li><strong>Class aptent taciti socios</strong><span>molestie sed luctus quis feugiat in pede Fusce tellus</span></li>
      <li><strong>Fusce ultricies orci</strong><span>Fusce tellus Sed metus augue aliquet felis at cursus</span></li>
    </ul>
    <a class="btn btn-red" href="#" style="left:31px;top:231px;width:102px">Read More</a>
  </section>
</main>

<footer class="site-footer">
  <nav class="footer-nav">
    <a href="#">Home</a><span class="sep">|</span><a href="#">About Us</a><span class="sep">|</span><a href="#">Services</a><span class="sep">|</span><a href="#">Dog Training</a><span class="sep">|</span><a href="#">Testimonials</a><span class="sep">|</span><a href="#">Dog Care</a><span class="sep">|</span><a href="#">Contact</a>
  </nav>
  <p class="copyright">© 2014 Company Name &nbsp;All right reserved &nbsp;Term of Use</p>
  <div class="social">
    <span role="img" aria-label="Social link"></span>
    <span role="img" aria-label="Social link"></span>
    <span role="img" aria-label="Social link"></span>
  </div>
</footer>

</body>
</html>
```